Pull Up Banner - Recruitment Company

We would like a design for a pull up banner.

For context: we are a recruitment business. We specialise in helping people in healthcare industry to find jobs in Australia.

I have come up with several ideas and text for the banner. Feel free to use the following as you see appropriate:

- Our logo (see attached)
- 'Healthcare Recruitment Agency'
- Some sort of imagine / cartoon of medical professionals (ie. doctor, nurse, physiotherapist, speech pathologist). A cartoon is more friendly than committing to a photo
- 'Empowering your next career move'
- 'Discover tailored opportunities based on your career preferences'
- Dot points (allied health, nursing, medical imaging)
- Contact info at the bottom including our website (www.quellastaffing.com.au, our Instagram handle @quellastaffing, Mobile: XXXX XXX XXX. The title section for contact information could be 'Get in touch:'

Feel free to submit a couple of designs and we can merge aspects that look good on your designs and find the perfect fit.
Thank you
Updates

Hello,

Thank you for your initial submissions to this project. I appreciate the time you've invested.

After reviewing the first attempt, I'd like to share some feedback and initial observations:

- Professionalism and engagement: Is the overall appearance of the banner professional? It's crucial that we have a high-quality design as this will represent our business.

- Image selection: The image (whether cartoon or real people) appears quite generic. Please consider submitting the banner with a few different photos in the middle for us to choose from. Ensure the image is a good fit and not simply a generic stock photo.

- Contact section: Kindly remove the phone number; we no longer wish to include it on the banner. Instead, please include our website (www.quellastaffing.com.au) and Instagram handle (@quellastaffing).

- Color scheme: White, black, and red/pink are preferred, or alternatively, blue. However, please avoid incorporating too many different colors as it may detract from the professional appearance.

We will be printing the design on a banner and require it to look professional and engaging.

Thank you once again for your submissions. I hope the feedback provided above is helpful.

Warm regards,

Target Market(s)

Allied Health Australia

Font styles to use
Serif

Colors
0054AA
0677BA
7BADD7
CADEEF
E8F1F8
0094D4
00A9DD
6FCCEA
C7EBF8
E9F6FB
EB3D1F
EC4F4E
F09395
F8D3D4
FCEDEE

```html
<!DOCTYPE html>
<html lang="en">
<head>
<meta charset="utf-8">
<title>Quella Staffing – Pull Up Banner</title>
<link href="https://fonts.googleapis.com/css2?family=Poppins:wght@400;500;600;700;800&display=swap" rel="stylesheet">
<style>
  :root {
    --navy: #17223d;
    --slate-blue: #6479b0;
    --sky-blue: #7fb0ef;
    --pale-blue: #dde6f5;
    --mist: #f3f5fb;
    --white: #ffffff;
  }
  * { box-sizing: border-box; margin: 0; padding: 0; }
  html, body { width: 672px; height: 1200px; overflow: hidden; background: var(--white); }
  .banner {
    position: relative;
    width: 672px;
    height: 1200px;
    background: var(--white);
    font-family: "Poppins", sans-serif;
    color: var(--navy);
    overflow: hidden;
  }
  .brand {
    position: absolute;
    left: 72px;
    top: 58px;
    font-size: 44px;
    font-weight: 700;
    letter-spacing: 3px;
    line-height: 1;
    color: var(--navy);
  }
  .brand-rule {
    position: absolute;
    left: 72px;
    top: 114px;
    width: 160px;
    height: 9px;
    background: var(--navy);
  }
  .headline {
    position: absolute;
    left: 70px;
    top: 150px;
    font-size: 67px;
    font-weight: 700;
    line-height: 56px;
    letter-spacing: -0.5px;
  }
  .headline span { display: block; }
  .headline .line-healthcare { color: var(--slate-blue); }
  .headline .line-recruitment { color: var(--navy); }
  .headline .line-agency { color: var(--sky-blue); font-weight: 500; }
  .hero {
    position: absolute;
    left: 50px;
    top: 330px;
    width: 600px;
    height: 390px;
  }
  .tagline {
    position: absolute;
    left: 0;
    width: 100%;
    top: 730px;
    text-align: center;
    font-size: 29px;
    font-weight: 700;
    line-height: 28px;
  }
  .tagline .accent { display: block; color: var(--slate-blue); }
  .intro {
    position: absolute;
    left: 0;
    width: 100%;
    top: 802px;
    text-align: center;
    font-size: 20px;
    line-height: 24px;
    font-weight: 400;
  }
  .contact-band { position: absolute; left: 0; top: 0; width: 672px; height: 1200px; }
  .specialties {
    position: absolute;
    left: 0;
    top: 870px;
    width: 100%;
    display: flex;
    justify-content: space-between;
    padding: 0 58px;
  }
  .specialty { width: 130px; text-align: center; color: var(--white); }
  .specialty-badge {
    width: 96px;
    height: 96px;
    margin: 0 auto;
    border-radius: 50%;
    border: 2px solid var(--sky-blue);
    display: flex;
    align-items: center;
    justify-content: center;
  }
  .specialty-badge .disc {
    width: 82px;
    height: 82px;
    border-radius: 50%;
    background: var(--pale-blue);
    display: flex;
    align-items: center;
    justify-content: center;
  }
  .specialty-label { margin-top: 8px; font-size: 21px; font-weight: 500; line-height: 21px; }
  .specialty.single .specialty-label { margin-top: 18px; }
  .social-pill {
    position: absolute;
    left: 50%;
    top: 1036px;
    transform: translateX(-50%);
    height: 30px;
    padding: 0 16px 0 12px;
    border-radius: 15px;
    background: var(--sky-blue);
    display: flex;
    align-items: center;
    gap: 8px;
    font-size: 17px;
    font-weight: 600;
    letter-spacing: 1px;
    color: var(--navy);
  }
  .social-pill .square { width: 16px; height: 16px; border-radius: 3px; background: var(--white); }
  .phone {
    position: absolute;
    left: 0;
    width: 100%;
    top: 1072px;
    display: flex;
    justify-content: center;
    align-items: center;
    gap: 10px;
    color: var(--white);
    font-size: 52px;
    font-weight: 700;
    letter-spacing: 1px;
    line-height: 1;
  }
  .website {
    position: absolute;
    left: 0;
    width: 100%;
    top: 1122px;
    text-align: center;
    color: var(--white);
    font-size: 23px;
    letter-spacing: 3px;
  }
  .website strong { color: var(--sky-blue); font-weight: 600; }
</style>
</head>
<body>
<div class="banner">
  <div class="brand">QUELLA STAFFING</div>
  <div class="brand-rule"></div>

  <h1 class="headline">
    <span class="line-healthcare">HEALTHCARE</span>
    <span class="line-recruitment">RECRUITMENT</span>
    <span class="line-agency">AGENCY</span>
  </h1>

  <svg class="hero" viewBox="0 0 600 390" xmlns="http://www.w3.org/2000/svg">
    <defs>
      <radialGradient id="heroFill" cx="50%" cy="50%" r="60%">
        <stop offset="0%" stop-color="#e4eaf6"/>
        <stop offset="100%" stop-color="#f3f5fb"/>
      </radialGradient>
    </defs>
    <circle cx="210" cy="150" r="135" fill="#17223d"/>
    <path d="M360 5 A190 190 0 0 1 360 385" fill="none" stroke="#6479b0" stroke-width="14"/>
    <circle cx="325" cy="195" r="190" fill="url(#heroFill)" role="img" aria-label="Illustration of a medical imaging scanner with a patient on the table and a doctor at a monitor"/>
  </svg>

  <h2 class="tagline">EMPOWERING YOUR NEXT<span class="accent">CAREER MOVE</span></h2>
  <p class="intro">Discover tailored opportunities based on<br>your career preferences</p>

  <svg class="contact-band" viewBox="0 0 672 1200" xmlns="http://www.w3.org/2000/svg" aria-hidden="true">
    <path d="M0 905 C120 935 250 950 380 930 C500 910 600 885 672 815 L672 1200 L0 1200 Z" fill="#17223d"/>
  </svg>

  <div class="specialties">
    <div class="specialty">
      <div class="specialty-badge"><div class="disc">
        <svg width="40" height="40" viewBox="0 0 40 40"><path d="M20 34 C8 25 4 18 4 13 A8 8 0 0 1 20 10 A8 8 0 0 1 36 13 C36 18 32 25 20 34Z" fill="#17223d"/><path d="M18 12h4v4h4v4h-4v4h-4v-4h-4v-4h4z" fill="#fff"/></svg>
      </div></div>
      <div class="specialty-label">Allied<br>health</div>
    </div>
    <div class="specialty single">
      <div class="specialty-badge"><div class="disc">
        <svg width="40" height="40" viewBox="0 0 40 40"><path d="M15 4h10v11h11v10H25v11H15V25H4V15h11z" fill="#17223d"/></svg>
      </div></div>
      <div class="specialty-label">Nursing</div>
    </div>
    <div class="specialty">
      <div class="specialty-badge"><div class="disc">
        <svg width="40" height="40" viewBox="0 0 40 40"><rect x="5" y="7" width="30" height="21" rx="3" fill="#17223d"/><rect x="9" y="11" width="22" height="13" fill="#dde6f5"/><rect x="17" y="28" width="6" height="5" fill="#17223d"/><rect x="11" y="33" width="18" height="3" fill="#17223d"/></svg>
      </div></div>
      <div class="specialty-label">Medical<br>imaging</div>
    </div>
  </div>

  <div class="social-pill"><span class="square"></span>@quellastaffing</div>

  <div class="phone">
    <svg width="40" height="40" viewBox="0 0 40 40" aria-hidden="true"><circle cx="20" cy="20" r="19" fill="#dde6f5"/><path d="M13 10c2 0 3 4 3 5s-2 2-2 3c1 3 4 6 7 7 1 0 2-2 3-2s5 1 5 3-2 4-4 4C16 30 10 24 10 14c0-2 1-4 3-4z" fill="#17223d"/></svg>
    <span>900 1234 5678</span>
  </div>
  <div class="website">www.<strong>quellastaffing</strong>.com.au</div>
</div>
</body>
</html>
```